sydney wedding photography business needs a business card design

we need a business card design for a sydney based wedding photography and videography business. our business name is :golden hour studio and film. our target clients are 24-35 yrs female. our style is candid, organic, natural, dynamic. we are a team of young photographers and videographers, and help brides to create memories that they will cherish for the rest of their lives. the logo will be provided. we want an elegant design that reflects our style, and also want to give a great impression to our clients that we are one of the best studios in sydney and our brand means quality and premium service.

Target Market(s)

bride to be, 24-35 years old, living in sydney and surrunding areas

Industry/Entity Type

Wedding Photography

Contact Information for Business Card

address: 57 tarrant street, glenmore nsw 2047
mobile: 0431872259
phone: (02) 9163 2408
info@tidewillowstudio.net.au
www.tidewillowstudio.net.au
facebook:tidewillowweddings
instagram:tidewillowweddings

Font styles to use
Serif
Sans Serif

Requirements
Nice to have
• maybe add my slogan"memories beyond eternity" if the layout looks good
Should not have
• no black color, not good idea for wedding biz card

```html
<!DOCTYPE html>
<html lang="en">
<head>
<meta charset="utf-8">
<title>Golden Hour Studio and Film – Business Card</title>
<link rel="stylesheet" href="https://fonts.googleapis.com/css2?family=Arimo:wght@400;700&display=swap">
<style>
  :root {
    --page-bg: #e9e4da;
    --card-white: #fbfbfb;
    --pattern-tone: #ececec;
    --band-mocha: #4a3828;
    --band-mocha-deep: #3a2c1f;
    --gold: #d6aa2a;
    --ink: #3a2e24;
    --sky-light: #7fa3c4;
    --sky-mid: #45688c;
    --sky-dark: #22384f;
  }
  html, body {
    margin: 0;
    padding: 0;
    width: 1200px;
    height: 858px;
    overflow: hidden;
    background: var(--page-bg);
    font-family: "Arimo", Arial, sans-serif;
  }
  .canvas {
    width: 1200px;
    height: 858px;
    display: flex;
    align-items: center;
    justify-content: center;
    gap: 40px;
  }
  .card {
    position: relative;
    width: 540px;
    height: 330px;
    overflow: hidden;
    box-shadow: 0 10px 28px rgba(0,0,0,0.22);
  }
  /* Front */
  .card-front { background: var(--card-white); }
  .front-texture {
    position: absolute; inset: 0;
    background: radial-gradient(ellipse at center, var(--card-white) 0%, var(--pattern-tone) 100%);
  }
  .front-bands { position: absolute; inset: 0; }
  .brand-name {
    position: absolute;
    left: 0; right: 0;
    top: 78px;
    text-align: center;
    color: var(--gold);
    font-weight: 700;
    font-size: 30px;
    line-height: 1.1;
    letter-spacing: 0.5px;
  }
  .contact-row {
    position: absolute;
    left: 0; right: 0;
    top: 158px;
    display: flex;
    justify-content: center;
    gap: 70px;
    color: var(--ink);
    font-size: 14px;
  }
  .contact-item {
    display: flex;
    flex-direction: column;
    align-items: center;
    gap: 4px;
  }
  .contact-line {
    position: absolute;
    left: 0; right: 0;
    text-align: center;
    color: var(--ink);
    font-size: 13px;
    line-height: 16px;
  }
  .contact-line.web { top: 206px; }
  .contact-line.address { top: 229px; font-size: 15px; line-height: 18px; }
  .icon { width: 13px; height: 13px; display: block; }
  .inline-icon { display: inline-block; vertical-align: -2px; margin-right: 5px; }
  /* Back */
  .card-back { background: var(--sky-mid); }
  .back-photo {
    position: absolute; inset: 0;
    background: linear-gradient(160deg, var(--sky-light) 0%, var(--sky-mid) 45%, var(--sky-dark) 100%);
  }
  .back-brand {
    position: absolute;
    left: 0; right: 0;
    top: 128px;
    text-align: center;
    color: var(--gold);
    font-weight: 700;
    font-size: 34px;
    line-height: 1.1;
  }
</style>
</head>
<body>
<main class="canvas">
  <section class="card card-front" aria-label="Business card front">
    <div class="front-texture" role="img" aria-label="Soft light grey damask background pattern"></div>
    <svg class="front-bands" viewBox="0 0 540 330" width="540" height="330" aria-hidden="true">
      <path d="M0 0 H540 V38 Q270 10 0 38 Z" fill="var(--band-mocha)"/>
      <path d="M0 38 Q270 10 540 38 V46 Q270 18 0 46 Z" fill="var(--gold)"/>
      <path d="M0 46 Q270 18 540 46 V50 Q270 22 0 50 Z" fill="var(--band-mocha-deep)"/>
      <path d="M0 330 H540 V292 Q270 320 0 292 Z" fill="var(--band-mocha)"/>
      <path d="M0 292 Q270 320 540 292 V284 Q270 312 0 284 Z" fill="var(--gold)"/>
      <path d="M0 284 Q270 312 540 284 V280 Q270 308 0 280 Z" fill="var(--band-mocha-deep)"/>
    </svg>
    <div class="brand-name">Golden Hour<br>Studio and Film</div>
    <div class="contact-row">
      <div class="contact-item">
        <svg class="icon" viewBox="0 0 12 12" aria-hidden="true">
          <rect x="3" y="0.5" width="6" height="11" rx="1.2" fill="var(--ink)"/>
          <rect x="4" y="1.8" width="4" height="7" fill="var(--card-white)"/>
          <circle cx="6" cy="10.1" r="0.6" fill="var(--card-white)"/>
        </svg>
        <span>0431872259</span>
      </div>
      <div class="contact-item">
        <svg class="icon" viewBox="0 0 12 12" aria-hidden="true">
          <path d="M1 4 Q6 1 11 4 V5.5 H8.5 V4.5 H3.5 V5.5 H1 Z" fill="var(--ink)"/>
          <rect x="2" y="6" width="8" height="5.5" rx="1" fill="var(--ink)"/>
        </svg>
        <span>(02) 9163 2408</span>
      </div>
    </div>
    <div class="contact-line web">
      <svg class="icon inline-icon" viewBox="0 0 12 12" aria-hidden="true"><circle cx="6" cy="6" r="5" fill="none" stroke="var(--ink)"/><path d="M1 6 H11 M6 1 V11" stroke="var(--ink)" stroke-width="0.8"/></svg>www.tidewillowstudio.net.au / info@tidewillowstudio.net.au
    </div>
    <div class="contact-line address">
      <svg class="icon inline-icon" viewBox="0 0 12 12" aria-hidden="true"><path d="M6 11.5 C2 7 2 5.5 2 4.5 A4 4 0 0 1 10 4.5 C10 5.5 10 7 6 11.5 Z" fill="var(--ink)"/></svg>57 tarrant street, glenmore nsw 2047
    </div>
  </section>

  <section class="card card-back" aria-label="Business card back">
    <div class="back-photo" role="img" aria-label="Wedding photograph of a couple under a white umbrella on a jetty beneath a stormy blue sky"></div>
    <div class="back-brand">Golden Hour<br>Studio and Film</div>
  </section>
</main>
</body>
</html>
```